New design for Comparison website

We need new design for our website https://prisvaktposten.no/ . We compare prices and providers in different niches such as electricity, mobile plans, broadband etc.

We would like to see design like Tarivo com or our competitor kjøpklokt no

We will need design of all pages, with tables, tables are somewhat different depending on the service compared (use kjøpklokt no for reference) . Our focus is CTR through comparison Tables.

Final design must communicate following: Professionalism, thrust, authority.

Number of Pages Required

5+ page

Font styles to use
Sans Serif

Colors

Designer to choose colors to be used in the design.

Requirements
Must have
• Tables
Nice to have
• Images in content

```html
<!DOCTYPE html>
<html lang="en">
<head>
<meta charset="utf-8">
<title>Prisvaktposten – Compare providers</title>
<link href="https://fonts.googleapis.com/css2?family=Mulish:wght@300;400;600;700&display=swap" rel="stylesheet">
<style>
:root{
  --green:#0fa56f;
  --green-dark:#0a8a5c;
  --blue:#14a2e2;
  --card-blue:#2a9ce0;
  --card-blue-edge:#1c86c9;
  --card-green:#14ad75;
  --card-green-edge:#0c9461;
  --card-yellow:#dcc500;
  --card-yellow-edge:#c7b000;
  --ink:#2b2b2b;
  --muted:#9a9a9a;
  --grey-band:#efefef;
  --line:#d9d9d9;
  --footer:#0b3424;
  --footer-text:#b9c9c0;
  --white:#ffffff;
}
*{margin:0;padding:0;box-sizing:border-box}
html,body{width:1200px;height:2980px;overflow:hidden}
body{font-family:"Mulish",sans-serif;color:var(--ink);background:var(--white);position:relative}
.abs{position:absolute}
.center{text-align:center;left:0;width:1200px}

/* header */
.site-header{position:absolute;top:0;left:0;width:1200px;height:106px;background:var(--white)}
.brand{position:absolute;left:120px;top:34px;display:flex;align-items:center;gap:12px}
.brand-mark{width:30px;height:30px;border-radius:50%;background:var(--green)}
.brand-name{font-size:25px;font-weight:700;color:var(--green)}
.main-nav{position:absolute;left:412px;top:0;display:flex;gap:28px;height:106px;align-items:center}
.main-nav a{font-size:16px;color:#555;text-decoration:none;position:relative;height:106px;line-height:106px}
.main-nav a.active{color:var(--green)}
.main-nav a.active::before{content:"";position:absolute;top:0;left:0;right:0;height:3px;background:var(--green)}

/* hero */
.hero{position:absolute;top:106px;left:0;width:1200px;height:580px;background:linear-gradient(120deg,#0b8f5e 0%,#10a46e 50%,#0c8d5c 100%)}
.hero-title{top:196px;font-size:41px;font-weight:400;color:var(--white);line-height:1.1}
.hero-sub{top:250px;font-size:33px;color:var(--white)}
.btn-outline{position:absolute;border:2px solid var(--white);color:var(--white);font-size:17px;display:flex;align-items:center;justify-content:center}
.hero .btn-outline{left:508px;top:312px;width:178px;height:46px}
.dots{position:absolute;top:544px;left:540px;display:flex;gap:8px}
.dots span{width:14px;height:14px;border-radius:50%;background:var(--white)}
.dots span.off{background:none;border:2px solid var(--white)}

/* sections */
.section-title{position:absolute;font-size:28px;font-weight:400;color:var(--ink)}
.step{position:absolute;top:796px;width:286px;height:244px;border:2px solid #d6d6d6;border-radius:14px;text-align:center}
.step-icon{position:absolute;left:90px;top:22px;width:108px;height:108px;border-radius:50%;background:var(--green)}
.step-num{position:absolute;left:-6px;top:-8px;width:28px;height:28px;border-radius:50%;background:#0b6e48;color:var(--white);font-size:14px;font-weight:700;line-height:28px}
.step h3{position:absolute;top:144px;left:0;width:100%;font-size:19px;font-weight:400}
.step p{position:absolute;top:176px;left:18px;right:18px;font-size:12px;line-height:20px;color:var(--muted)}

.categories{position:absolute;top:1096px;left:0;width:1200px;height:382px;background:linear-gradient(100deg,#10a870 0%,#0fa993 45%,#12a0e2 100%)}
.notch{position:absolute;top:1096px;left:572px;width:0;height:0;border-left:28px solid transparent;border-right:28px solid transparent;border-top:26px solid var(--white)}
.cat{position:absolute;top:1250px;text-align:center;color:var(--white);font-size:18px}
.cat svg{display:block;margin:0 auto 14px}
.categories .btn-outline{left:524px;top:312px;width:152px;height:36px;font-size:13px;letter-spacing:.5px}

.plan{position:absolute;top:1588px;width:270px;height:306px;border-radius:14px;color:var(--white);text-align:center}
.plan h3{position:absolute;top:98px;width:100%;font-size:20px;font-weight:400}
.plan p{position:absolute;top:136px;left:42px;right:42px;font-size:12px;line-height:20px}
.plan .btn-outline{left:68px;top:232px;width:134px;height:42px;border-radius:21px;font-size:14px}
.plan svg{position:absolute;top:26px;left:115px}
.plan.blue{left:178px;background:var(--card-blue);border:5px solid var(--card-blue-edge)}
.plan.green{left:466px;background:var(--card-green);border:5px solid var(--card-green-edge)}
.plan.yellow{left:752px;background:var(--card-yellow);border:5px solid var(--card-yellow-edge)}

.testimonials{position:absolute;top:1936px;left:0;width:1200px;height:364px;background:var(--grey-band);border-top:2px solid var(--line);border-bottom:2px solid var(--line)}
.author-photo{position:absolute;left:210px;top:122px;width:156px;height:156px;border-radius:50%;background:radial-gradient(circle at 50% 40%,#d9cfc8,#b9c0c6)}
.quote{position:absolute;left:380px;top:140px;width:640px;font-size:17px;line-height:28px;color:#333}
.author{position:absolute;left:382px;top:252px;font-size:16px;font-weight:700}
.arrow{position:absolute;top:178px}

.newsletter-title{top:2356px;font-size:30px;color:var(--green)}
.newsletter-sub{top:2406px;font-size:17px;color:var(--muted)}
.email-field{position:absolute;left:270px;top:2456px;width:496px;height:42px;border:2px solid #cfcfcf;background:#f4f4f4;display:flex;align-items:center;padding-left:16px;gap:12px;font-size:12px;color:#888}
.signup-btn{position:absolute;left:774px;top:2456px;width:154px;height:42px;background:var(--green);color:var(--white);font-size:15px;display:flex;align-items:center;justify-content:center}

.site-footer{position:absolute;top:2578px;left:0;width:1200px;height:402px;background:var(--footer);color:var(--footer-text)}
.foot-col{position:absolute;top:70px}
.foot-col h4{font-size:16px;font-weight:600;color:var(--white);margin-bottom:12px;letter-spacing:.3px}
.foot-col a{display:block;font-size:15px;color:var(--footer-text);text-decoration:none;line-height:32px}
.socials{display:flex;gap:10px;margin-top:4px}
.socials span{width:36px;height:36px;border-radius:50%;border:2px solid var(--white)}
.foot-brand{position:absolute;left:712px;top:200px;display:flex;align-items:center;gap:12px}
.foot-brand .brand-name{font-size:24px}
.foot-rule{position:absolute;left:146px;top:330px;width:950px;height:1px;background:#2b5443}
.copyright{top:354px;font-size:12px;color:#8aa497}
</style>
</head>
<body>

<header class="site-header">
  <div class="brand"><span class="brand-mark"></span><span class="brand-name">Prisvaktposten</span></div>
  <nav class="main-nav">
    <a class="active" href="#">Home</a><a href="#">Broadband</a><a href="#">MMS</a><a href="#">Current</a><a href="#">Hosting &amp; Domain</a><a href="#">Residential Alarm</a>
  </nav>
</header>

<section class="hero" role="img" aria-label="Photo of hands typing on a laptop, tinted green">
  <h1 class="abs center hero-title">Morbi diam mauris viverra in</h1>
  <p class="abs center hero-sub">gravida eu mattis in ante</p>
  <a class="btn-outline">Compare Now</a>
  <div class="dots"><span class="off"></span><span></span><span></span><span></span></div>
</section>

<h2 class="section-title center" style="top:730px">How it Works</h2>

<div class="step" style="left:152px">
  <div class="step-icon"><span class="step-num">1</span>
    <svg width="108" height="108" viewBox="0 0 108 108" fill="none" stroke="#fff" stroke-width="2"><circle cx="54" cy="54" r="22" stroke-dasharray="5 5"/><circle cx="54" cy="32" r="4" fill="#fff"/><circle cx="54" cy="76" r="4" fill="#fff"/><circle cx="32" cy="54" r="4" fill="#fff"/><circle cx="76" cy="54" r="4" fill="#fff"/></svg>
  </div>
  <h3>Select Category</h3>
  <p>We collect the most relevant information about the service in one place</p>
</div>
<div class="step" style="left:460px">
  <div class="step-icon"><span class="step-num">2</span>
    <svg width="108" height="108" viewBox="0 0 108 108" fill="none" stroke="#fff" stroke-width="2"><circle cx="40" cy="36" r="5"/><circle cx="68" cy="72" r="5"/><path d="M45 36h19v30" stroke-dasharray="4 4"/><path d="M63 72H40V42" stroke-dasharray="4 4"/><path d="M60 30l5 6-5 6M48 66l-5 6 5 6"/></svg>
  </div>
  <h3>Compare Providers</h3>
  <p>The best and most reputable players compared so you can choose the one</p>
</div>
<div class="step" style="left:770px">
  <div class="step-icon"><span class="step-num">3</span>
    <svg width="108" height="108" viewBox="0 0 108 108" fill="none" stroke="#fff" stroke-width="2"><path d="M34 48l20-16 20 16v26H34z"/><path d="M34 48l20 14 20-14"/><rect x="46" y="42" width="16" height="14"/></svg>
  </div>
  <h3>Order Service</h3>
  <p>Order the service and enjoy that you've got the best provider quickly and easily.</p>
</div>

<section class="categories">
  <h2 class="section-title center" style="top:54px;font-size:24px;color:#fff">Look through the Available Categories</h2>
  <div class="btn-outline">VIEW MORE</div>
</section>
<div class="notch"></div>

<div class="cat" style="left:172px;width:100px">
  <svg width="46" height="72" viewBox="0 0 46 72" fill="none" stroke="#fff" stroke-width="3"><rect x="8" y="4" width="7" height="14"/><rect x="20" y="4" width="7" height="14"/><rect x="32" y="4" width="7" height="14"/><path d="M4 22h38v22a10 10 0 0 1-10 10H14A10 10 0 0 1 4 44z"/><path d="M14 32h18M14 40h18M23 54v14"/></svg>Electricity</div>
<div class="cat" style="left:318px;width:124px">
  <svg width="46" height="72" viewBox="0 0 46 72" fill="none" stroke="#fff" stroke-width="3"><rect x="6" y="2" width="34" height="66" rx="5"/><path d="M6 12h34M6 56h34"/><circle cx="23" cy="62" r="2" fill="#fff"/></svg>Mobile Plans</div>
<div class="cat" style="left:488px;width:120px">
  <svg width="76" height="72" viewBox="0 0 76 72" fill="#fff"><rect x="14" y="2" width="6" height="34"/><rect x="56" y="2" width="6" height="34"/><rect x="2" y="36" width="72" height="24" rx="3"/><rect x="10" y="60" width="8" height="8"/><rect x="58" y="60" width="8" height="8"/><rect x="12" y="44" width="6" height="6" fill="#10a99a"/><rect x="24" y="44" width="6" height="6" fill="#10a99a"/><rect x="36" y="44" width="6" height="6" fill="#10a99a"/></svg>Broadband</div>
<div class="cat" style="left:648px;width:180px">
  <svg width="80" height="72" viewBox="0 0 80 72" fill="none" stroke="#fff" stroke-width="3"><circle cx="40" cy="38" r="20"/><path d="M40 28c6 6 8 10 4 16a6 6 0 0 1-9-6c2 2 4 0 5-10z" fill="#fff"/><path d="M14 20a30 30 0 0 0 0 36M66 20a30 30 0 0 1 0 36M22 10"/></svg>Residential Alarm</div>
<div class="cat" style="left:866px;width:182px">
  <svg width="70" height="72" viewBox="0 0 70 72" fill="none" stroke="#fff" stroke-width="3"><rect x="3" y="4" width="64" height="58" rx="2"/><path d="M3 14h64"/><ellipse cx="35" cy="30" rx="12" ry="4"/><path d="M23 30v20c0 2 5 4 12 4s12-2 12-4V30M23 40c0 2 5 4 12 4s12-2 12-4"/></svg>Hosting &amp; Domain</div>

<h2 class="section-title center" style="top:1522px">Comparison Tables</h2>

<div class="plan blue">
  <svg width="40" height="60" viewBox="0 0 40 60" fill="none" stroke="#fff" stroke-width="3"><rect x="4" y="2" width="32" height="56" rx="4"/><path d="M4 10h32M4 48h32"/></svg>
  <h3>Mobiles Plan</h3>
  <p>Class aptent taciti sociosqu ad litora torquent per conubia nostra per inceptos hymenaeos Proin nulla arcu nonummy luctus</p>
  <div class="btn-outline">Learn More</div>
</div>
<div class="plan green">
  <svg width="40" height="60" viewBox="0 0 46 72" fill="none" stroke="#fff" stroke-width="3"><rect x="8" y="4" width="7" height="14"/><rect x="20" y="4" width="7" height="14"/><rect x="32" y="4" width="7" height="14"/><path d="M4 22h38v22a10 10 0 0 1-10 10H14A10 10 0 0 1 4 44z"/><path d="M14 32h18M14 40h18M23 54v14"/></svg>
  <h3>Electricity Plan</h3>
  <p>Class aptent taciti sociosqu ad litora torquent per conubia nostra per inceptos hymenaeos Proin nulla arcu nonummy luctus</p>
  <div class="btn-outline">Learn More</div>
</div>
<div class="plan yellow">
  <svg width="56" height="60" viewBox="0 0 76 72" fill="#fff" style="left:107px"><rect x="14" y="2" width="6" height="34"/><rect x="56" y="2" width="6" height="34"/><rect x="2" y="36" width="72" height="24" rx="3"/><rect x="10" y="60" width="8" height="8"/><rect x="58" y="60" width="8" height="8"/></svg>
  <h3>Broadband Plan</h3>
  <p>Class aptent taciti sociosqu ad litora torquent per conubia nostra per inceptos hymenaeos Proin nulla arcu nonummy luctus</p>
  <div class="btn-outline">Learn More</div>
</div>

<section class="testimonials">
  <h2 class="section-title center" style="top:70px">Testimonials</h2>
  <svg class="arrow" style="left:124px" width="20" height="36" viewBox="0 0 20 36" fill="none" stroke="#aaa" stroke-width="3"><path d="M18 2L3 18l15 16"/></svg>
  <svg class="arrow" style="left:1040px" width="20" height="36" viewBox="0 0 20 36" fill="none" stroke="#aaa" stroke-width="3"><path d="M2 2l15 16L2 34"/></svg>
  <div class="author-photo" role="img" aria-label="Portrait photo of the customer giving the testimonial"></div>
  <p class="quote">“Maecenas aliquet velit vel turpis Mauris neque metus malesuada nec ultricies sit amet porttitor mattis enim In massa libero interdum nec interdum vel blandit sed nulla”</p>
  <p class="author">By Author Name</p>
</section>

<h2 class="section-title center newsletter-title">Sign Up for Our Newsletters</h2>
<p class="abs center newsletter-sub">Get news and deals delivered right to your inbox.</p>
<div class="email-field">
  <svg width="18" height="14" viewBox="0 0 18 14" fill="none" stroke="#999" stroke-width="1.5"><rect x="1" y="1" width="16" height="12"/><path d="M1 1l8 7 8-7"/></svg>Email address
</div>
<div class="signup-btn">CLICK HERE</div>

<footer class="site-footer">
  <div class="foot-col" style="left:156px"><h4>COMPANY</h4><a>Home</a><a>About us</a><a>Contact</a><a>Terms</a><a>Privacy</a></div>
  <div class="foot-col" style="left:326px"><h4>SUBLINKS</h4><a>Cheap mms</a><a>Current</a><a>To me</a><a>Web hosting</a></div>
  <div class="foot-col" style="left:500px"><h4>RESOURCES</h4><a>Residential Alarm</a><a>Broadband</a><a>Support</a><a>Contact Us</a></div>
  <div class="foot-col" style="left:726px"><h4>STAY IN TOUCH</h4>
    <div class="socials" aria-label="Social media links"><span></span><span></span><span></span><span></span></div>
  </div>
  <div class="foot-brand"><span class="brand-mark"></span><span class="brand-name">Prisvaktposten</span></div>
  <div class="foot-rule"></div>
  <p class="abs center copyright">© 2017 Company Name. All right reserved</p>
</footer>

</body>
</html>
```